International emerging specialist Research and Development Company focused on plant-based medicine

We need a powerpoint design for a new company based in British Columbia, Canada called Tavrel Phytocor. We are focused on developing plant-based medicines. The company is driven by its experience in research and development work in plant genetics, cultivation techniques, natural medicines, biochemistry, agriculture and technologies. Tavrel will research, develop and produce very unique and specific cultivars from the plant kingdom needed for specific ailments in medical patients. We would like to see designs that use our current logo and its colour scheme. The final design should communicate financial safety, growth, and research and development.

```html
<!DOCTYPE html>
<html lang="en">
<head>
<meta charset="utf-8">
<title>Tavrel Phytocor – Table Slide</title>
<link rel="stylesheet" href="https://fonts.googleapis.com/css2?family=Roboto+Condensed:wght@300;400&family=Open+Sans:wght@400;600&family=Roboto:wght@400;700&display=swap">
<style>
  :root {
    --brand-red: #d3141c;
    --heading-red: #b3151c;
    --slide-bg: #f3f3f3;
    --footer-grey: #d2d2d2;
    --body-grey: #9a9a9a;
    --cell-text: #222222;
    --row-grey: #e0e0e0;
    --row-pink: #f7d9dc;
    --white: #ffffff;
  }
  * { box-sizing: border-box; margin: 0; padding: 0; }
  html, body { width: 1200px; height: 900px; overflow: hidden; }
  body { background: var(--slide-bg); font-family: "Roboto", Arial, sans-serif; }

  .slide { position: relative; width: 1200px; height: 900px; background: var(--slide-bg); }

  .slide-header {
    position: absolute; left: 0; top: 0; width: 1200px; height: 93px;
    background: var(--brand-red);
    display: flex; align-items: center; justify-content: space-between;
    padding: 0 20px 0 30px;
  }
  .slide-title {
    font-family: "Roboto Condensed", Arial, sans-serif;
    font-weight: 400; font-size: 48px; color: var(--white); letter-spacing: 0;
  }
  .brand-name {
    font-family: "Roboto Condensed", Arial, sans-serif;
    font-weight: 300; font-size: 46px; color: var(--white); text-transform: lowercase;
  }

  .intro { position: absolute; left: 88px; top: 170px; width: 1020px; }
  .intro-heading { font-size: 22px; font-weight: 700; color: var(--heading-red); }
  .intro-body {
    margin-top: 18px; margin-left: 9px;
    font-size: 16.5px; line-height: 25.5px; color: var(--body-grey);
  }

  .data-table { position: absolute; left: 96px; top: 324px; width: 1008px; }
  .table-row {
    display: grid; grid-template-columns: 346px 348px auto;
    align-items: center;
  }
  .table-head {
    height: 60px; background: var(--brand-red); padding-left: 21px;
    font-family: "Open Sans", Arial, sans-serif; font-weight: 600;
    font-size: 24px; color: var(--white); text-transform: uppercase;
  }
  .table-body-row {
    height: 59px; margin-top: 5px; padding-left: 25px;
    font-family: "Open Sans", Arial, sans-serif; font-size: 19px; color: var(--cell-text);
  }
  .table-head + .table-body-row { margin-top: 4px; }
  .row-grey { background: var(--row-grey); }
  .row-pink { background: var(--row-pink); }

  .slide-footer {
    position: absolute; left: 0; bottom: 0; width: 1200px; height: 42px;
    background: var(--footer-grey);
  }
</style>
</head>
<body>
<main class="slide">
  <header class="slide-header">
    <h1 class="slide-title">Project Title Here</h1>
    <span class="brand-name">Tavrel</span>
  </header>

  <section class="intro">
    <h2 class="intro-heading">Table Head Here</h2>
    <p class="intro-body">Lorem ipsum dolor sit Lorem ipsum dolor sit&nbsp; Lorem ipsum dolor sit Lorem ipsum dolor sit&nbsp; Lorem ipsum dolor sit Lorem ipsum dolor&nbsp; Lorem ipsum dolor sit Lorem ipsum dolor sit&nbsp; Lorem ipsum dolor sit Lorem ipsum dolor sit&nbsp; Lorem ipsum dolor sit Lorem ipsum dolor&nbsp; Lorem ipsum dolor sit Lorem ipsum dolor sit&nbsp; Lorem ipsum dolor sit Lorem ipsum dolor sit</p>
  </section>

  <section class="data-table">
    <div class="table-row table-head"><span>Table Head Here</span><span>Table Head Here</span><span>Table Head Here</span></div>
    <div class="table-row table-body-row row-grey"><span>Subtext here Subtext here</span><span>Subtext here Subtext here</span><span>Subtext here Subtext here</span></div>
    <div class="table-row table-body-row row-pink"><span>Subtext here Subtext here</span><span>Subtext here Subtext here</span><span>Subtext here Subtext here</span></div>
    <div class="table-row table-body-row row-grey"><span>Subtext here Subtext here</span><span>Subtext here Subtext here</span><span>Subtext here Subtext here</span></div>
    <div class="table-row table-body-row row-pink"><span>Subtext here Subtext here</span><span>Subtext here Subtext here</span><span>Subtext here Subtext here</span></div>
    <div class="table-row table-body-row row-grey"><span>Subtext here Subtext here</span><span>Subtext here Subtext here</span><span>Subtext here Subtext here</span></div>
    <div class="table-row table-body-row row-pink"><span>Subtext here Subtext here</span><span>Subtext here Subtext here</span><span>Subtext here Subtext here</span></div>
  </section>

  <footer class="slide-footer"></footer>
</main>
</body>
</html>
```